Pellmore's Pick magazine ad

This is a full page ad in a magazine announcing that I won The Pick Of Pellmore Valley Realtor for 2023. The dimensions for the full page ad are 7.125" x 9.75"
I would like it to say "Thank You Harford County for voting me Pellmore's Pick Realtor for 2022 & 2023!"

I am honored that the residents of this county have recognized my integrity, values, willingness to go above and beyond, to save my clients tons of money and stress, and to constantly pour back into this community.

If you are ever thinking about buying or selling a house, please don't hesitate to reach out, I am available 24/7 by text or phone call to save you money and provide the best top notch service:

Corwin Ashlund
call/text 410-555-0172

Small at the bottom:
www.MarlowCrestHomes.com
2749 W Amberly Ln, Bel Air, MD 21014
833-555-0149

I am attaching my logo, the Pellmore's Pick 2023 logo, my picture, and last years ad (I'm hoping to make this years ad different and better)

```html
<!DOCTYPE html>
<html lang="en">
<head>
<meta charset="utf-8">
<title>Pellmore's Pick Realtor – Full Page Ad</title>
<link href="https://fonts.googleapis.com/css2?family=Montserrat:ital,wght@0,300;0,400;0,800;1,300&family=Allura&display=swap" rel="stylesheet">
<style>
  :root {
    --backdrop: #e9e9e9;
    --paper: #f7f7f7;
    --navy: #1d2d5c;
    --ink: #3a3a3a;
    --script-grey: #7a7a7a;
    --orange: #e46f24;
    --badge: #2b2b2b;
    --band-black: #111111;
    --band-grey: #9c9c9c;
    --white: #ffffff;
  }
  * { margin: 0; padding: 0; box-sizing: border-box; }
  html, body { width: 1200px; height: 960px; overflow: hidden; background: var(--backdrop); }
  body { font-family: "Montserrat", sans-serif; color: var(--ink); }

  .ad-page {
    position: absolute; left: 264px; top: 20px;
    width: 672px; height: 920px;
    background: var(--paper);
    overflow: hidden;
  }

  .realtor-photo {
    position: absolute; left: 405px; top: 90px;
    width: 267px; height: 830px;
    background: linear-gradient(180deg, #d8d8d8 0%, #8f8f8f 45%, #4a4a4a 100%);
  }

  .team-mark {
    position: absolute; left: 100px; top: 46px; width: 280px;
    text-align: center; color: var(--navy); font-weight: 400;
  }
  .team-mark__dot {
    width: 54px; height: 54px; margin: 0 auto 12px;
    border-radius: 50%; background: var(--navy);
  }
  .team-mark__name { font-size: 16px; letter-spacing: .8px; line-height: 1.2; white-space: nowrap; }
  .team-mark__sub { font-size: 7.5px; letter-spacing: 1.5px; text-transform: uppercase; margin-top: 5px; }

  .thank-you {
    position: absolute; left: 26px; top: 205px;
    font-family: "Allura", cursive; font-weight: 400; font-size: 98px; line-height: 1;
    color: var(--script-grey); white-space: nowrap;
  }

  .headline { position: absolute; left: 34px; top: 345px; width: 360px; }
  .headline__lead { font-weight: 300; font-size: 17px; color: var(--navy); }
  .headline__award {
    font-weight: 800; font-size: 28px; color: var(--orange);
    text-transform: uppercase; margin: 4px 0 4px; letter-spacing: .3px; white-space: nowrap;
  }
  .headline__year { font-weight: 300; font-size: 17px; color: var(--navy); }

  .badges { position: absolute; left: 40px; top: 465px; display: flex; gap: 26px; }
  .badges svg { width: 62px; height: 62px; }

  .message {
    position: absolute; left: 30px; top: 572px; width: 250px;
    font-style: italic; font-weight: 300; font-size: 10px; line-height: 1.75;
    text-align: center; color: var(--ink);
  }
  .message p + p { margin-top: 14px; }

  .contact-band {
    position: absolute; left: 0; top: 780px; height: 62px; width: 420px;
    background: var(--navy); color: var(--white);
    display: flex; align-items: center; padding-left: 26px;
    font-weight: 300; font-size: 24px; white-space: nowrap;
  }
  .name-band {
    position: absolute; left: 420px; top: 780px; height: 62px; width: 252px;
    background: var(--band-black); color: var(--white);
    display: flex; align-items: center; padding-left: 18px;
    font-weight: 400; font-size: 20px; letter-spacing: 1px; white-space: nowrap;
  }
  .details-band {
    position: absolute; left: 0; top: 842px; height: 78px; width: 420px;
    background: linear-gradient(180deg, var(--band-grey), #c4c4c4);
    color: var(--white); padding: 12px 26px;
    font-size: 10.5px; line-height: 1.8; font-weight: 400;
  }
</style>
</head>
<body>
  <main class="ad-page">
    <div class="realtor-photo" role="img" aria-label="Black and white portrait of the realtor in a blazer and open-collar shirt"></div>

    <div class="team-mark">
      <div class="team-mark__dot"></div>
      <div class="team-mark__name">THE MARLOW CREST TEAM</div>
      <div class="team-mark__sub">at Hearthline Real Estate</div>
    </div>

    <h1 class="thank-you">Thank You</h1>

    <div class="headline">
      <p class="headline__lead">Harford County for voting me</p>
      <p class="headline__award">Pellmore's Pick</p>
      <p class="headline__year">REALTOR for 2022 &amp; 2023!</p>
    </div>

    <div class="badges" aria-label="Award badges 2022 and 2023">
      <svg viewBox="0 0 64 64"><circle cx="32" cy="32" r="31" fill="var(--badge)"/></svg>
      <svg viewBox="0 0 64 64"><circle cx="32" cy="32" r="31" fill="var(--badge)"/></svg>
    </div>

    <div class="message">
      <p>I am honored that the residents of this county have recognized my integrity, values, willingness to go above and beyond, to save my clients tons of money and stress, and to constantly pour back into this community.</p>
      <p>If you are ever thinking about buying or selling a house, please don't hesitate to reach out, I am available 24/7 by text or phone call to save you money and provide the best top notch service:</p>
    </div>

    <div class="contact-band">call/text 410-555-0172</div>
    <div class="name-band">Corwin Ashlund</div>
    <div class="details-band">
      <p>www.MarlowCrestHomes.com</p>
      <p>2749 W Amberly Ln, Bel Air, MD 21014</p>
      <p>833-555-0149</p>
    </div>
  </main>
</body>
</html>
```